3 graphic designs for my website

Hello
I need 3 graphic designs saved as a jpeg. 50x50mm, able to resize a small amount without losing quality. Its for a travel website, I wish you to create 3 graphic images with the same theme.
1 that says 'Hotels'
1 that says 'Holidays'
1 thats says 'Our Deals'
Colours to include only, white,#4ea6dc,#808080(small amount of this colour) , #ff9933.
So the graphic can contain a hotel/beach/plane etc but want to keep it simple and not to busy
Travel

```html
<!DOCTYPE html>
<html lang="en">
<head>
<meta charset="UTF-8">
<title>Discounted Holidays</title>
<link href="https://fonts.googleapis.com/css2?family=Tenor+Sans&display=swap" rel="stylesheet">
<style>
  :root {
    --brand-blue: #2a86dc;
    --band-blue: #2f7fe0;
    --panel-top: #ffffff;
    --panel-bottom: #dcdcdc;
    --sky: #4ea6dc;
    --sky-light: #b8dcf2;
    --sea: #4ea6dc;
    --shore: #f4f8fb;
    --sand-light: #ffe6cc;
    --sand: #ffc78f;
  }
  html, body {
    margin: 0;
    padding: 0;
    width: 1200px;
    height: 1200px;
    overflow: hidden;
  }
  .tile {
    position: relative;
    width: 1200px;
    height: 1200px;
    background: linear-gradient(180deg, var(--panel-top) 68%, var(--panel-bottom) 100%);
    overflow: hidden;
  }
  .tile__art {
    position: absolute;
    inset: 0;
    width: 1200px;
    height: 1200px;
  }
  .tile__headline {
    position: absolute;
    left: 0;
    right: 0;
    top: 948px;
    text-align: center;
    font-family: "Tenor Sans", sans-serif;
    color: var(--brand-blue);
    margin: 0;
    font-weight: 400;
  }
  .tile__kicker {
    display: block;
    font-size: 56px;
    line-height: 1;
    letter-spacing: 1px;
  }
  .tile__title {
    display: block;
    margin-top: 2px;
    font-size: 118px;
    line-height: 1;
    letter-spacing: 2px;
  }
</style>
</head>
<body>
<div class="tile">
  <svg class="tile__art" viewBox="0 0 1200 1200" xmlns="http://www.w3.org/2000/svg">
    <defs>
      <linearGradient id="beachScene" x1="0" y1="0" x2="0" y2="1">
        <stop offset="0" stop-color="var(--sky)"/>
        <stop offset="0.36" stop-color="var(--sky-light)"/>
        <stop offset="0.40" stop-color="var(--sea)"/>
        <stop offset="0.56" stop-color="var(--sea)"/>
        <stop offset="0.64" stop-color="var(--shore)"/>
        <stop offset="0.74" stop-color="var(--sand-light)"/>
        <stop offset="1" stop-color="var(--sand)"/>
      </linearGradient>
    </defs>
    <path class="tile__photo" role="img" aria-label="Photo of a tropical beach with palm trees, golden sand and calm blue sea"
          d="M0 0 H1200 V790 C950 760 620 800 420 870 C320 905 180 905 0 820 Z"
          fill="url(#beachScene)"/>
    <path class="tile__wave-band"
          d="M0 820 C180 905 320 905 420 870 C620 800 950 760 1200 790 V812 C950 786 640 820 440 886 C320 928 170 918 0 840 Z"
          fill="var(--band-blue)"/>
  </svg>
  <h1 class="tile__headline">
    <span class="tile__kicker">DISCOUNTED</span>
    <span class="tile__title">HOLIDAYS</span>
  </h1>
</div>
</body>
</html>
```